The Linen Loft Co

We need a business card design for our wardrobe company.
Please visit our website www.gentlelinenlofts.com to get an idea of who we are.

```html
<!DOCTYPE html>
<html lang="en">
<head>
<meta charset="utf-8">
<title>The Linen Loft Co — Business Card</title>
<link rel="stylesheet" href="https://fonts.googleapis.com/css2?family=Roboto:wght@400;500&display=swap">
<style>
  :root {
    --backdrop: #c9c9c9;
    --photo-dark: #1c1b1a;
    --photo-mid: #3a3836;
    --photo-light: #55524f;
    --paper: #ffffff;
    --ink: #1a1a1a;
    --accent-grey: #9a9a9a;
    --light-text: #ffffff;
  }
  * { box-sizing: border-box; margin: 0; padding: 0; }
  html, body {
    width: 1200px; height: 930px; overflow: hidden;
    background: var(--backdrop);
    font-family: "Roboto", sans-serif;
  }
  .card {
    position: absolute;
    left: 270px;
    width: 660px; height: 377px;
    border-radius: 26px;
    overflow: hidden;
    box-shadow: 0 10px 24px rgba(0,0,0,.25);
  }
  .card--front { top: 62px; }
  .card--back { top: 491px; }

  .photo {
    position: absolute; inset: 0;
    background:
      linear-gradient(180deg, rgba(255,255,255,.10) 0 12%, transparent 12% 100%),
      radial-gradient(ellipse at 55% 55%, var(--photo-light) 0%, var(--photo-mid) 40%, var(--photo-dark) 100%);
  }

  .brand { position: absolute; display: flex; align-items: center; gap: 14px; }
  .brand__mark { width: 22px; height: 22px; border: 2px solid currentColor; flex: none; }
  .brand__name { font-weight: 500; font-size: 19px; letter-spacing: .5px; text-transform: uppercase; line-height: 1.2; }
  .brand__tagline { font-weight: 500; font-size: 16px; margin-top: 4px; }

  .card--front .brand { left: 250px; top: 160px; color: var(--light-text); }

  .curve { position: absolute; inset: 0; }
  .card--back .brand { left: 330px; top: 72px; color: var(--ink); }

  .contact {
    position: absolute; left: 48px; top: 180px;
    color: var(--light-text);
  }
  .contact__name { font-weight: 500; font-size: 25px; letter-spacing: .5px; text-transform: uppercase; }
  .contact__role { font-size: 15px; margin: 4px 0 10px; }
  .contact__address { font-size: 15px; line-height: 1.4; margin-bottom: 8px; }
  .contact__list { list-style: none; font-size: 15px; line-height: 1.65; }
  .contact__list li { display: flex; align-items: center; gap: 10px; }
  .contact__list svg { width: 13px; height: 13px; flex: none; }
</style>
</head>
<body>

<section class="card card--front">
  <div class="photo" role="img" aria-label="Dim photograph of a walk-in wardrobe with shelves and hanging clothes"></div>
  <div class="brand">
    <span class="brand__mark"></span>
    <div>
      <div class="brand__name">The Linen Loft Co</div>
      <div class="brand__tagline">Every Shelf in its Place</div>
    </div>
  </div>
</section>

<section class="card card--back">
  <div class="photo" role="img" aria-label="Dim photograph of a walk-in wardrobe with shelves and hanging clothes"></div>
  <svg class="curve" viewBox="0 0 660 377" preserveAspectRatio="none" aria-hidden="true">
    <path d="M128 0 Q 270 330 660 350 L660 332 Q 290 308 150 0 Z" fill="var(--accent-grey)"/>
    <path d="M150 0 Q 290 308 660 332 L660 0 Z" fill="var(--paper)"/>
  </svg>
  <div class="brand">
    <span class="brand__mark"></span>
    <div>
      <div class="brand__name">The Linen Loft Co</div>
      <div class="brand__tagline">Every Shelf in its Place</div>
    </div>
  </div>

  <div class="contact">
    <h2 class="contact__name">Daniel Hartley</h2>
    <p class="contact__role">Director</p>
    <p class="contact__address">Harbour House, 42 Mill Lane,<br>London N4 8QT</p>
    <ul class="contact__list">
      <li>
        <svg viewBox="0 0 16 16"><path fill="currentColor" d="M3.6 1.5l2.3 2.8-1.3 1.6c.9 2 2.5 3.6 4.5 4.5l1.6-1.3 2.8 2.3-1.4 2.1C7.4 13.3 2.7 8.6 1.5 3z"/></svg>
        0207 555 0148
      </li>
      <li>
        <svg viewBox="0 0 16 16"><rect x="1.5" y="3.5" width="13" height="9" fill="none" stroke="currentColor" stroke-width="1.4"/><path d="M1.5 3.5l6.5 5 6.5-5" fill="none" stroke="currentColor" stroke-width="1.4"/></svg>
        info@gentlelinenlofts.com
      </li>
      <li>
        <svg viewBox="0 0 16 16"><circle cx="8" cy="8" r="6.3" fill="none" stroke="currentColor" stroke-width="1.3"/><ellipse cx="8" cy="8" rx="2.8" ry="6.3" fill="none" stroke="currentColor" stroke-width="1.1"/><path d="M1.7 8h12.6" stroke="currentColor" stroke-width="1.1"/></svg>
        www.gentlelinenlofts.com
      </li>
    </ul>
  </div>
</section>

</body>
</html>
```